Redesign Of Current Landing Page

I need to redesign this landing page https://www.brightlanepromo.biz/?page=landing&landing=23 (Please do not opt in because when you do it will show you the home page. Please clear your cookies before going to this url above to view the 1 page landing page.)

Please use my updated website as a reference for colors and logo.
http://sitecradlewerk.com/dh/bpq/index.html

I would like the call to action to be a button that opens into a lead form...

Button would be "Download Samples"

Target Market(s)

small business owners

Industry/Entity Type

Marketing

Number of Pages Required

1 page

Colors

Designer to choose colors to be used in the design.

Requirements
Must have
• must be full responsive on all devices
Nice to have
• must have a legitimate professional apeal to it
Should not have
• open

```html
<!DOCTYPE html>
<html lang="en">
<head>
<meta charset="utf-8">
<title>Bright Lane Promo Group – Incentives Landing Page</title>
<link href="https://fonts.googleapis.com/css2?family=Lato:wght@400;700;900&display=swap" rel="stylesheet">
<style>
:root{
  --blue:#1b64b7;
  --blue-deep:#0f4f9c;
  --orange:#f7941d;
  --orange-dark:#e07f0c;
  --text:#333;
  --grey-bg:#eeeeee;
  --footer-bg:#c9c9c9;
  --white:#fff;
}
*{margin:0;padding:0;box-sizing:border-box}
html,body{width:1200px;height:3030px;overflow:hidden}
body{font-family:'Lato',Arial,sans-serif;color:var(--text);background:var(--white);position:relative}
.cta{display:block;width:448px;height:56px;line-height:56px;text-align:center;background:var(--orange);color:#1d1d1d;font-weight:700;font-size:18px;text-transform:uppercase;text-decoration:none;border-bottom:3px solid var(--orange-dark);letter-spacing:.2px}
.cta.centered{margin:0 auto}
.section-title{font-weight:900;font-size:31px;color:var(--blue);text-transform:uppercase;letter-spacing:.5px}

/* Hero */
.hero{position:absolute;left:0;top:0;width:1200px;height:665px;overflow:hidden}
.hero-photo{position:absolute;inset:0;background:linear-gradient(180deg,#6a5b8a 0%,#8a7a9e 22%,#4d4a6e 45%,#2d3d68 62%,#1f3a72 80%,#27508f 100%)}
.hero-photo::after{content:"";position:absolute;left:520px;top:140px;width:700px;height:360px;background:radial-gradient(ellipse at 60% 50%,rgba(235,170,90,.45),rgba(0,0,0,0) 65%)}
.brand{position:absolute;left:132px;top:38px;display:flex;align-items:center;gap:10px}
.brand-dot{width:30px;height:30px;border-radius:50%;background:var(--blue)}
.brand-name{font-weight:900;font-size:30px;color:var(--white);letter-spacing:1px}
.contact{position:absolute;right:130px;top:22px;display:flex;gap:32px;color:var(--white);font-weight:700;font-size:16px}
.contact span{display:flex;align-items:center;gap:10px}
.contact svg{width:22px;height:22px}
.hero-box{position:absolute;left:320px;top:190px;width:560px;height:312px;background:rgba(40,40,50,.55);border:2px solid rgba(255,255,255,.35);text-align:center;color:var(--white);padding-top:26px}
.hero-box h1{font-weight:900;font-size:40px;line-height:46px;text-transform:uppercase}
.hero-box .lead{font-size:24px;line-height:27px;margin-top:6px}
.hero-box .sub{font-size:16.5px;line-height:22px;margin-top:16px}
.hero-box .cta{position:absolute;left:55px;top:253px}

/* Imagine */
.imagine{position:absolute;left:0;top:665px;width:1200px;height:605px;background:var(--grey-bg)}
.imagine .section-title{position:absolute;left:130px;top:58px}
.imagine-box{position:absolute;left:130px;top:125px;width:600px;height:300px;border:2px solid #dedede;background:#f2f2f2;padding:34px 36px 0 38px;font-size:14.6px;line-height:21px;color:#333}
.imagine-box p{margin-bottom:21px;width:490px}
.incentive-stack{position:absolute;left:700px;top:110px;width:360px;height:340px;background:linear-gradient(135deg,#2a4f8c,#7a3e6e 45%,#1d2e4a 70%,#c47a2a);border-radius:4px;transform:rotate(-2deg)}
.imagine .cta{position:absolute;left:130px;top:465px}

/* How */
.how{position:absolute;left:0;top:1270px;width:1200px;height:470px;overflow:hidden}
.how-photo{position:absolute;inset:0;background:linear-gradient(180deg,#2a78c8 0%,#1d6cc0 40%,#175fb1 70%,#1a5ea8 100%)}
.how-inner{position:relative;text-align:center;color:var(--white);padding-top:56px}
.how .section-title{color:var(--orange)}
.how p{width:700px;margin:0 auto;font-size:14.6px;line-height:21px}
.how p.first{margin-top:28px}
.how p.second{margin-top:38px;width:560px}
.how .cta{margin-top:58px}

/* Why */
.why{position:absolute;left:0;top:1740px;width:1200px;height:645px;background:var(--white);text-align:center}
.why .section-title{padding-top:88px;line-height:40px}
.benefits{position:absolute;left:120px;top:230px;width:960px;display:flex;justify-content:space-between}
.benefit{width:160px;display:flex;flex-direction:column;align-items:center}
.benefit-icon{width:136px;height:136px;border-radius:50%;border:2px solid var(--blue);display:flex;align-items:center;justify-content:center}
.benefit-icon svg{width:70px;height:70px}
.benefit-label{margin-top:38px;font-size:12.5px;line-height:18px;color:#222}
.why .cta{position:absolute;left:376px;top:500px}

/* Testimonials */
.testimonials{position:absolute;left:0;top:2385px;width:1200px;height:583px;background:#ececec;text-align:center}
.testimonials .section-title{padding-top:72px}
.quote{position:absolute;left:325px;top:160px;width:550px;font-size:14.6px;line-height:26px;color:#333}
.quote-mark{position:absolute;font-family:Georgia,serif;font-weight:700;font-size:72px;color:#333;line-height:1}
.quote-mark.open{left:288px;top:128px}
.quote-mark.close{left:797px;top:308px}
.author{position:absolute;left:0;top:370px;width:1200px;font-size:11px;line-height:19px}
.author strong{color:var(--blue);font-weight:700;display:block}
.testimonials .cta{position:absolute;left:376px;top:453px}

/* Footer */
.site-footer{position:absolute;left:0;top:2968px;width:1200px;height:62px;background:var(--footer-bg);text-align:center;line-height:62px;font-size:11.5px;color:#444}
</style>
</head>
<body>

<header class="hero">
  <div class="hero-photo" role="img" aria-label="Luxury resort villa with an infinity pool at dusk"></div>
  <div class="brand"><span class="brand-dot"></span><span class="brand-name">BLPG</span></div>
  <div class="contact">
    <span><svg viewBox="0 0 24 24"><circle cx="12" cy="12" r="12" fill="#f7941d"/><path d="M8 6.5l2 0 1 3-1.4 1a7 7 0 003.9 3.9l1-1.4 3 1v2c0 .7-.6 1.2-1.3 1.1A10 10 0 016.9 7.8C6.8 7.1 7.3 6.5 8 6.5z" fill="#fff"/></svg>1-800-555-0142</span>
    <span><svg viewBox="0 0 24 24"><circle cx="12" cy="12" r="12" fill="#f7941d"/><circle cx="12" cy="12" r="6" fill="none" stroke="#fff" stroke-width="1.8"/><path d="M12 8.5V12l2.3 1.5" stroke="#fff" stroke-width="1.8" fill="none"/></svg>MON-FRI 8AM-5PM PST</span>
  </div>
  <div class="hero-box">
    <h1>Attract More<br>Customers</h1>
    <p class="lead">who spend more money with your<br>business more often!</p>
    <p class="sub">Using Free Vacation &amp; Cruise Certificates And Other<br>Incentives Without Breaking The Bank!</p>
    <a class="cta" href="#">Download Free Samples of Our Incentives</a>
  </div>
</header>

<section class="imagine">
  <h2 class="section-title">Imagine</h2>
  <div class="imagine-box">
    <p>Being able to create exciting give away promotions that will boost your sales without ever having to worry about cost.</p>
    <p>Bright Lane Promo Group, Inc. provides high-perceived value promotional incentives to businesses that want to advertise an exciting Give Away that will instantly attract more customers from your existing advertising efforts.</p>
    <p>Your business can give away incentive certificates that are redeemable for luxury hotel &amp; resort stays with airfare included, cruises, cash for gas, groceries, dining and even electronic goods.</p>
  </div>
  <div class="incentive-stack" role="img" aria-label="Fanned stack of printed incentive certificates for cruises, cash back and travel"></div>
  <a class="cta" href="#">Download Free Samples of Our Incentives</a>
</section>

<section class="how">
  <div class="how-photo" role="img" aria-label="Tropical overwater bungalows with palm trees under a blue tint"></div>
  <div class="how-inner">
    <h2 class="section-title">How Can We Do It?</h2>
    <p class="first">We help fill empty rooms for thousands of hotels and resorts in hundreds of destinations around the world as well as the major cruise lines. Hotels and resorts are rarely full so when we place someone in their empty rooms, they end up making it up when travelers spend money on room service, spa services, eat at their in-house restaurants, casino and take advantage of other amenities that drive revenue.</p>
    <p class="second">We also help over 18,000 restaurants, electronic manufacturers, the major gas companies and top grocery chains in the U.S and Canada increase brand awareness as well as increase customer loyalty.</p>
    <a class="cta centered" href="#">Download Free Samples of Our Incentives</a>
  </div>
</section>

<section class="why">
  <h2 class="section-title">Why Offer Incentives<br>to Customers?</h2>
  <div class="benefits">
    <div class="benefit">
      <div class="benefit-icon"><svg viewBox="0 0 70 70" fill="none" stroke="#1b64b7" stroke-width="3"><path d="M8 8v54h56"/><rect x="18" y="42" width="6" height="16" fill="#1b64b7"/><rect x="29" y="36" width="6" height="22" fill="#1b64b7"/><rect x="40" y="40" width="6" height="18" fill="#1b64b7"/><rect x="51" y="30" width="6" height="28" fill="#1b64b7"/><path d="M14 38l14-14 10 8 20-18"/><path d="M50 14h8v8"/></svg></div>
      <p class="benefit-label">Increase Responses<br>From Your Existing Ads</p>
    </div>
    <div class="benefit">
      <div class="benefit-icon"><svg viewBox="0 0 70 70" fill="#1b64b7"><circle cx="26" cy="28" r="13"/><circle cx="26" cy="28" r="5" fill="#fff"/><g stroke="#1b64b7" stroke-width="6"><path d="M26 9v38M7 28h38M13 15l26 26M13 41l26-26"/></g><circle cx="26" cy="28" r="5" fill="#fff"/><circle cx="50" cy="48" r="9"/><g stroke="#1b64b7" stroke-width="4"><path d="M50 35v26M37 48h26M41 39l18 18M41 57l18-18"/></g><circle cx="50" cy="48" r="3.5" fill="#fff"/></svg></div>
      <p class="benefit-label">#1 Sales Closing Tool -<br>Gift w/ Purchase</p>
    </div>
    <div class="benefit">
      <div class="benefit-icon"><svg viewBox="0 0 70 70"><path d="M24 40l-10 24 9-4 5 8 8-20zM46 40l10 24-9-4-5 8-8-20z" fill="#1b64b7"/><circle cx="35" cy="26" r="20" fill="#1b64b7"/><circle cx="35" cy="26" r="13" fill="#fff"/><path d="M35 17l3 6 6 .8-4.5 4.2 1.1 6.2L35 31l-5.6 3.2 1.1-6.2L26 23.8l6-.8z" fill="#1b64b7"/></svg></div>
      <p class="benefit-label">Build Brand<br>Awareness and Trust</p>
    </div>
    <div class="benefit">
      <div class="benefit-icon"><svg viewBox="0 0 70 70" fill="#1b64b7"><path d="M35 6l14 5v11c0 9-6 15-14 18-8-3-14-9-14-18V11z"/><path d="M6 34l4-2 8 16 12 4v10H18L6 48z"/><path d="M64 34l-4-2-8 16-12 4v10h12l12-14z"/></svg></div>
      <p class="benefit-label">Insure The Sale Over<br>Your Competition</p>
    </div>
    <div class="benefit">
      <div class="benefit-icon"><svg viewBox="0 0 70 70" fill="#1b64b7"><path d="M2 24h10v22H2zM58 24h10v22H58z"/><path d="M14 26l12-4 10 3 8-3 12 4v18l-10 8-6 2-4-3-6 2-8-8-8-2z"/><path d="M30 30l8 2 10 10" stroke="#fff" stroke-width="2" fill="none"/></svg></div>
      <p class="benefit-label">Boost Repeat and<br>Referral Business-</p>
    </div>
    <div class="benefit">
      <div class="benefit-icon"><svg viewBox="0 0 70 70" fill="none" stroke="#1b64b7" stroke-width="4"><path d="M14 30a22 22 0 0138-12"/><path d="M54 8v12H42"/><path d="M56 40a22 22 0 01-38 12"/><path d="M16 62V50h12"/><text x="35" y="44" font-family="Lato, Arial, sans-serif" font-weight="900" font-size="24" fill="#1b64b7" stroke="none" text-anchor="middle">$</text></svg></div>
      <p class="benefit-label">Improve<br>Retention Rates</p>
    </div>
  </div>
  <a class="cta" href="#">Download Free Samples of Our Incentives</a>
</section>

<section class="testimonials">
  <h2 class="section-title">Testimonials</h2>
  <span class="quote-mark open">&ldquo;</span>
  <p class="quote">I began using your incentives two years ago to boost lead generation efforts. I have experienced a 63% increase in lead captures. And, even more importantly, my sales have increased as well. The ability to offer unlimited certificates and not having to pay for each certificate I give away is perhaps the best feature of the program, but having the flexibility to email or print certificates for my customers is also wonderful. I even use your html banners to automate my promotions right on my website!.</p>
  <span class="quote-mark close">&rdquo;</span>
  <p class="author"><strong>Dan R.</strong>Maple Grove, TN</p>
  <a class="cta" href="#">Download Free Samples of Our Incentives</a>
</section>

<footer class="site-footer">© 2017 Bright Lane Promo Group, Inc. - All Rights Reserved</footer>

</body>
</html>
```